Veltrane Group Business Card Design

The CEO is looking for a new trendy look for his business card.
You can stay with current branding or come up with something new/creative. It can be 3D, including Medical Office buildings. You can use our logo in a variety of colors. Please include name, title, company name, company website, email address, cell number

Target Market(s)

Real Estate Development and Construction

Industry/Entity Type

Health care real estate

Contact Information for Business Card

Rohesh Kamdar, CEO M-604.781.2249 E-roheshkamdar@veltrane.com Address:4180 Lindqvist Ave, Tampa, FL 33482 www.veltrane.com

Font styles to use
Other font styles liked:
• Be creative

Requirements
Must have
• Creative, trendy look
Nice to have
• Please go to our website to get a feel- www. veltrane.com
Should not have
• small fonts

```html
<!DOCTYPE html>
<html lang="en">
<head>
<meta charset="utf-8">
<title>Veltrane Group Business Card</title>
<link href="https://fonts.googleapis.com/css2?family=Montserrat:wght@400;700&display=swap" rel="stylesheet">
<style>
  :root {
    --stage: #2b2b2b;
    --card-dark: #161616;
    --card-light: #ffffff;
    --ink: #111111;
    --paper: #ffffff;
  }
  * { margin: 0; padding: 0; box-sizing: border-box; }
  html, body { width: 1200px; height: 875px; overflow: hidden; }
  body {
    background: var(--stage);
    font-family: "Montserrat", sans-serif;
    position: relative;
  }
  .card {
    position: absolute;
    width: 520px;
    height: 300px;
    border-radius: 22px;
  }
  .card-front {
    left: 90px; top: 150px;
    background: var(--card-dark);
    display: flex; align-items: center; justify-content: center;
  }
  .card-back {
    left: 590px; top: 420px;
    background: var(--card-light);
    color: var(--ink);
  }
  .company-name {
    font-weight: 700;
    font-size: 44px;
    line-height: 1;
    white-space: nowrap;
  }
  .card-front .company-name { color: var(--paper); }
  .card-back .company-name {
    position: absolute; left: 0; right: 0; top: 62px;
    text-align: center;
    color: var(--ink);
  }
  .contact-block {
    position: absolute; left: 0; right: 0; top: 170px;
    display: flex; align-items: center; justify-content: center; gap: 14px;
  }
  .person { text-align: right; }
  .person .name { font-weight: 700; font-size: 19px; }
  .person .title { font-size: 13px; }
  .divider { width: 1.5px; height: 66px; background: var(--ink); }
  .details { list-style: none; font-size: 13px; line-height: 21px; }
  .details li { display: flex; align-items: center; gap: 8px; }
  .details svg { width: 11px; height: 11px; fill: var(--ink); flex: none; }
  .address {
    position: absolute; left: 0; right: 0; bottom: 26px;
    text-align: center; font-size: 13px;
  }
</style>
</head>
<body>
  <section class="card card-front">
    <div class="company-name">Veltrane Group</div>
  </section>

  <section class="card card-back">
    <div class="company-name">Veltrane Group</div>
    <div class="contact-block">
      <div class="person">
        <div class="name">Rohesh Kamdar</div>
        <div class="title">CEO</div>
      </div>
      <div class="divider"></div>
      <ul class="details">
        <li><svg viewBox="0 0 24 24" aria-hidden="true"><path d="M6.6 10.8a15.1 15.1 0 0 0 6.6 6.6l2.2-2.2a1 1 0 0 1 1-.25 11.4 11.4 0 0 0 3.6.57 1 1 0 0 1 1 1V20a1 1 0 0 1-1 1A17 17 0 0 1 3 4a1 1 0 0 1 1-1h3.5a1 1 0 0 1 1 1c0 1.25.2 2.45.57 3.57a1 1 0 0 1-.25 1z"/></svg>604.781.2249</li>
        <li><svg viewBox="0 0 24 24" aria-hidden="true"><path d="M2 5h20v14H2z M2 5l10 8 10-8" fill="none" stroke="#111" stroke-width="2"/><path d="M2 5h20l-10 8z"/></svg>roheshkamdar@veltrane.com</li>
        <li><svg viewBox="0 0 24 24" aria-hidden="true"><circle cx="12" cy="12" r="10" fill="none" stroke="#111" stroke-width="2"/><path d="M2 12h20M12 2c3 3 3 17 0 20M12 2c-3 3-3 17 0 20" fill="none" stroke="#111" stroke-width="1.6"/></svg>www.veltrane.com</li>
      </ul>
    </div>
    <div class="address">4180 Lindqvist Ave, Tampa, FL 33482</div>
  </section>
</body>
</html>
```